Healthcare technology firm needs business card layout. Logo provided.

We need a business card design for a new healthcare technology company called BelnaVix.net. The logo is already done so that will be used in the design. We assist patients and their families manage their personal health finances. Our initial product is our web site membership that includes educational content on your health benefits, tools, and downloadable forms.

We would like to see designs that use our existing logo or extend the logo in a creative way. Should be very consumer friendly.

Industry/Entity Type

Healthcare

```html
<!DOCTYPE html>
<html lang="en">
<head>
<meta charset="utf-8">
<title>BelnaVix Business Card</title>
<link rel="stylesheet" href="https://fonts.googleapis.com/css2?family=Quicksand:wght@500;600&family=Arimo:wght@400&display=swap">
<style>
  :root {
    --page-bg: #e4e8f0;
    --card-black: #0c0c0d;
    --brand-blue: #1f6fe0;
    --band-blue: #1d4fb0;
    --brand-green: #4fd12a;
    --accent-cyan: #2fb4d8;
    --text-light: #f2f2f2;
    --text-grey: #c9c9c9;
  }
  * { margin: 0; padding: 0; box-sizing: border-box; }
  html, body {
    width: 1200px;
    height: 900px;
    overflow: hidden;
    background: var(--page-bg);
  }
  .canvas {
    position: relative;
    width: 1200px;
    height: 900px;
  }
  .card {
    position: absolute;
    left: 250px;
    width: 700px;
    height: 400px;
    background: var(--card-black);
    border-radius: 34px;
    overflow: hidden;
    box-shadow: 0 10px 30px rgba(20, 30, 60, 0.25);
  }
  .card--front { top: 40px; }
  .card--back { top: 460px; }

  .front-sweep {
    position: absolute;
    inset: 0;
    width: 700px;
    height: 400px;
  }

  .brand-name {
    font-family: "Quicksand", sans-serif;
    font-weight: 600;
    color: var(--brand-blue);
    letter-spacing: 1px;
    line-height: 1;
  }
  .card--front .brand-name {
    position: absolute;
    left: 48px;
    top: 62px;
    font-size: 66px;
  }
  .tagline {
    position: absolute;
    left: 50px;
    top: 150px;
    font-family: "Quicksand", sans-serif;
    font-weight: 500;
    font-size: 21px;
    color: var(--brand-green);
    letter-spacing: 0.5px;
  }
  .tagline .tagline-accent { color: var(--accent-cyan); }
  .tagline-rule {
    position: absolute;
    left: 46px;
    top: 182px;
    width: 380px;
    height: 2px;
    background: linear-gradient(90deg, rgba(47,180,216,0) 0%, var(--accent-cyan) 30%, var(--accent-cyan) 70%, rgba(47,180,216,0) 100%);
  }

  .person {
    position: absolute;
    left: 318px;
    top: 200px;
    font-family: "Arimo", sans-serif;
  }
  .person-name {
    font-size: 22px;
    color: var(--text-grey);
    letter-spacing: 0.5px;
  }
  .person-title {
    font-size: 12px;
    color: var(--text-grey);
    margin-top: 4px;
    margin-left: 10px;
  }

  .contact-list {
    position: absolute;
    left: 48px;
    top: 240px;
    list-style: none;
    font-family: "Arimo", sans-serif;
    font-size: 17px;
    color: var(--text-light);
  }
  .contact-item {
    display: flex;
    align-items: flex-start;
    gap: 14px;
    margin-bottom: 16px;
    line-height: 1.2;
  }
  .contact-item:nth-child(2) { margin-bottom: 6px; }
  .contact-icon {
    width: 18px;
    height: 18px;
    flex-shrink: 0;
    margin-top: 1px;
  }
  .web-domain { color: var(--accent-cyan); }

  .back-content {
    position: absolute;
    inset: 0;
    display: flex;
    flex-direction: column;
    align-items: center;
    justify-content: center;
    gap: 18px;
  }
  .card--back .brand-name { font-size: 72px; }
  .back-url {
    font-family: "Quicksand", sans-serif;
    font-weight: 600;
    font-size: 22px;
    color: var(--accent-cyan);
    letter-spacing: 1.5px;
  }
</style>
</head>
<body>
<main class="canvas">

  <section class="card card--front" aria-label="Business card front">
    <svg class="front-sweep" viewBox="0 0 700 400" aria-hidden="true">
      <defs>
        <linearGradient id="bandBlue" x1="0" y1="0" x2="1" y2="1">
          <stop offset="0" stop-color="#2a5ed0"/>
          <stop offset="1" stop-color="#163d98"/>
        </linearGradient>
        <linearGradient id="bandGreen" x1="0" y1="0" x2="0" y2="1">
          <stop offset="0" stop-color="#2f9a1e"/>
          <stop offset="0.5" stop-color="#57d62d"/>
          <stop offset="1" stop-color="#3fb022"/>
        </linearGradient>
      </defs>
      <path d="M470 0 C650 60 700 260 500 400 L700 400 L700 0 Z" fill="url(#bandBlue)"/>
      <path d="M470 0 C650 60 700 260 500 400 C615 270 600 95 470 0 Z" fill="url(#bandGreen)"/>
    </svg>

    <h1 class="brand-name">BelnaVix</h1>
    <p class="tagline">Making <span class="tagline-accent">Your Health</span> Costs Simpler</p>
    <div class="tagline-rule"></div>

    <div class="person">
      <p class="person-name">Marla J . Whitcombe</p>
      <p class="person-title">CEO</p>
    </div>

    <ul class="contact-list">
      <li class="contact-item">
        <svg class="contact-icon" viewBox="0 0 18 18" aria-hidden="true">
          <path d="M2 9 L9 3 L16 9" fill="none" stroke="#4fd12a" stroke-width="2" stroke-linejoin="round"/>
          <path d="M4 8 V15 H14 V8" fill="none" stroke="#4fd12a" stroke-width="2"/>
          <rect x="7.5" y="10.5" width="3" height="4.5" fill="#4fd12a"/>
        </svg>
        <span>Cedar Falls Pine Harbor<br>Ridgeview Lakemont</span>
      </li>
      <li class="contact-item">
        <svg class="contact-icon" viewBox="0 0 18 18" aria-hidden="true">
          <rect x="5" y="2" width="8" height="14" rx="1.5" fill="none" stroke="#4fd12a" stroke-width="2"/>
          <rect x="7" y="5" width="4" height="4" fill="#4fd12a"/>
        </svg>
        <span>239-555-0147</span>
      </li>
      <li class="contact-item">
        <svg class="contact-icon" viewBox="0 0 18 18" aria-hidden="true">
          <circle cx="9" cy="9" r="7" fill="none" stroke="#4fd12a" stroke-width="1.8"/>
          <ellipse cx="9" cy="9" rx="3" ry="7" fill="none" stroke="#4fd12a" stroke-width="1.4"/>
          <line x1="2" y1="9" x2="16" y2="9" stroke="#4fd12a" stroke-width="1.4"/>
        </svg>
        <span>www.<span class="web-domain">belnavix</span>.net</span>
      </li>
    </ul>
  </section>

  <section class="card card--back" aria-label="Business card back">
    <div class="back-content">
      <p class="brand-name">BelnaVix</p>
      <p class="back-url">www.belnavix.net</p>
    </div>
  </section>

</main>
</body>
</html>
```